Employee Benefits Flyer for Recruiting

We are a Steel Product Supplier and Manufacturer in Toledo Ohio.

We would like to create an "attention getting", one-page handout to give prospective employees (both production and administrative) that illustrates all the benefits we offer as a company. An editable document would be preferable as we add more or change existing benefits in the future. Current benefits include:

Individual and Family Medical Insurance
Dental Insurance
Vision Insurance
Short Term Disability Insurance
Critical Illness and Accident Insurance
No Cost Life Insurance Policy
Education Cost Reimbursement
401K with Company Match
Profit Sharing
Attendance and Performance Bonuses
No Cost Legal Assistance
No Cost Counseling Services
No Cost Tobacco Cessation Coaching
No Cost College Planning Assistance
No Cost Work-Life Services
No Cost Employee Discounts
No Cost Legal Consultation
No Cost Financial Consultation
No Cost ID Theft Assistance
No Cost Tax Consultation Assistance
Up to 17 Days of Paid Time Off

Target Market(s)

Potential Employees

Industry/Entity Type

Industrial Manufacturing

Requirements
Must have
• Nicely laid out illustrations / engaging content

```html
<!DOCTYPE html>
<html lang="en">
<head>
<meta charset="utf-8">
<title>We Are Hiring – Employee Benefits Flyer</title>
<link rel="stylesheet" href="https://fonts.googleapis.com/css2?family=Anton&family=Barlow+Condensed:wght@500;700&family=Kaushan+Script&family=Montserrat:wght@700&display=swap">
<style>
  :root {
    --stage: #141414;
    --blue-deep: #0a3fa8;
    --blue-bright: #0a6cff;
    --blue-dark: #06297a;
    --navy-text: #1b3c8c;
    --tick: #1f4ea3;
    --panel: #e6e6e6;
    --white: #ffffff;
    --silver: #bfbfbf;
  }
  * { margin: 0; padding: 0; box-sizing: border-box; }
  html, body {
    width: 1200px; height: 1200px; overflow: hidden;
    background: var(--stage);
  }
  .flyer {
    position: absolute; left: 200px; top: 34px;
    width: 800px; height: 1131px;
    background: var(--white); overflow: hidden;
  }
  .hero { position: absolute; left: 0; top: 0; width: 800px; height: 660px; }
  .brand {
    position: absolute; left: 600px; top: 22px; width: 180px;
    display: flex; flex-direction: column; align-items: center; gap: 12px;
  }
  .brand-dot { width: 70px; height: 70px; border-radius: 50%; background: var(--white); }
  .brand-name {
    font-family: "Barlow Condensed", sans-serif; font-weight: 700;
    font-size: 19px; letter-spacing: 1.5px; color: var(--white); white-space: nowrap;
  }
  .headline-script {
    position: absolute; left: 185px; top: 158px; width: 400px; text-align: center;
    font-family: "Kaushan Script", cursive; font-size: 98px; line-height: 1.1;
    color: var(--white); white-space: nowrap; transform: rotate(-4deg);
  }
  .headline-main {
    position: absolute; left: 150px; top: 262px; width: 500px; text-align: center;
    font-family: "Barlow Condensed", sans-serif; font-weight: 700;
    font-size: 176px; line-height: 1; letter-spacing: -2px; color: var(--white);
    white-space: nowrap;
  }
  .benefits-panel {
    position: absolute; left: 55px; top: 671px; width: 691px; height: 387px;
    background: var(--panel);
  }
  .offerings-tab { position: absolute; left: 0; top: 0; width: 420px; height: 740px; pointer-events: none; }
  .offerings-title {
    position: absolute; left: 68px; top: 636px;
    font-family: "Anton", sans-serif; font-size: 62px; line-height: 1;
    letter-spacing: 2px; color: var(--white);
  }
  .benefit-list {
    position: absolute; list-style: none;
    font-family: "Barlow Condensed", sans-serif; font-weight: 500;
    font-size: 20.5px; color: var(--navy-text); white-space: nowrap;
  }
  .benefit-list li { position: relative; padding-left: 30px; }
  .benefit-list li::before {
    content: ""; position: absolute; left: 5px; top: 50%;
    width: 7px; height: 13px; margin-top: -9px;
    border-right: 3.5px solid var(--tick); border-bottom: 3.5px solid var(--tick);
    transform: rotate(45deg);
  }
  .benefit-list--core { left: 76px; top: 730px; line-height: 31px; }
  .benefit-list--extra { left: 419px; top: 689px; line-height: 32.2px; }
  .footer-band {
    position: absolute; left: 0; bottom: 0; width: 800px; height: 48px;
    background: linear-gradient(90deg, var(--blue-deep), var(--blue-bright) 50%, var(--blue-deep));
    display: flex; align-items: center; justify-content: center;
    font-family: "Montserrat", sans-serif; font-weight: 700; font-size: 16px;
    letter-spacing: 3.5px; color: var(--white);
  }
</style>
</head>
<body>
<main class="flyer">
  <svg class="hero" viewBox="0 0 800 660" xmlns="http://www.w3.org/2000/svg">
    <defs>
      <linearGradient id="heroBlue" x1="0" y1="0" x2="1" y2="1">
        <stop offset="0" stop-color="#0a3fa8"/>
        <stop offset="0.45" stop-color="#0a6cff"/>
        <stop offset="1" stop-color="#0a3fa8"/>
      </linearGradient>
      <linearGradient id="photoTone" x1="0" y1="0" x2="1" y2="1">
        <stop offset="0" stop-color="#3b4350"/>
        <stop offset="0.45" stop-color="#7d7e80"/>
        <stop offset="0.7" stop-color="#2f6fa6"/>
        <stop offset="1" stop-color="#4a5a3a"/>
      </linearGradient>
      <linearGradient id="silverSweep" x1="0" y1="0" x2="1" y2="0">
        <stop offset="0" stop-color="#9e9e9e"/>
        <stop offset="0.5" stop-color="#d9d9d9"/>
        <stop offset="1" stop-color="#ffffff"/>
      </linearGradient>
    </defs>
    <rect class="hero-backdrop" width="800" height="660" fill="url(#heroBlue)"/>
    <path class="hero-photo" role="img" aria-label="Aerial photo of the steel plant building with its blue metal facade and roof"
          d="M0,115 C180,35 520,45 800,240 L800,385 C640,560 330,560 0,320 Z" fill="url(#photoTone)"/>
    <path class="silver-swoosh" d="M0,462 C220,610 560,640 800,380 L800,420 C560,660 220,640 0,520 Z" fill="url(#silverSweep)"/>
    <path class="white-base" d="M0,500 C220,640 560,650 800,410 L800,660 L0,660 Z" fill="#ffffff"/>
  </svg>

  <div class="brand">
    <span class="brand-dot"></span>
    <span class="brand-name">KEYSTONE METAL WORKS</span>
  </div>

  <div class="headline-script">We are</div>
  <div class="headline-main">HIRING</div>

  <div class="benefits-panel"></div>

  <svg class="offerings-tab" viewBox="0 0 420 740" xmlns="http://www.w3.org/2000/svg">
    <defs>
      <linearGradient id="tabBlue" x1="0" y1="0" x2="1" y2="0">
        <stop offset="0" stop-color="#0a3fa8"/>
        <stop offset="0.5" stop-color="#0a6cff"/>
        <stop offset="1" stop-color="#0a3fa8"/>
      </linearGradient>
    </defs>
    <path class="tab-fold" d="M31,690 L55,718 L55,734 Q38,726 32,712 Z" fill="#06297a"/>
    <path class="tab-face" d="M42,625 H392 Q401,625 398,634 L381,698 Q375,718 352,718 H55 Q33,718 31,700 L31,636 Q31,625 42,625 Z" fill="url(#tabBlue)"/>
  </svg>
  <div class="offerings-title">OFFERINGS</div>

  <ul class="benefit-list benefit-list--core">
    <li>Individual and Family Medical Insurance</li>
    <li>Dental Insurance</li>
    <li>Vision Insurance</li>
    <li>Short Term Disability Insurance</li>
    <li>Critical Illness and Accident Insurance</li>
    <li>No Cost Life Insurance Policy</li>
    <li>Education Cost Reimbursement</li>
    <li>401K with Company Match</li>
    <li>Profit Sharing</li>
    <li>Attendance and Performance Bonuses</li>
  </ul>

  <ul class="benefit-list benefit-list--extra">
    <li>No Cost Legal Assistance</li>
    <li>No Cost Counseling Services</li>
    <li>No Cost Tobacco Cessation Coaching</li>
    <li>No Cost College Planning Assistance</li>
    <li>No Cost Work-Life Services</li>
    <li>No Cost Employee Discounts</li>
    <li>No Cost Legal Consultation</li>
    <li>No Cost Financial Consultation</li>
    <li>No Cost ID Theft Assistance</li>
    <li>No Cost Tax Consultation Assistance</li>
    <li>Up to 17 Days of Paid Time Off</li>
  </ul>

  <footer class="footer-band">WWW.KEYSTONE-METALWORKS.COM</footer>
</main>
</body>
</html>
```